KDN Roofing Truck and Trailer Wrap

I need a graphic wrap on my Toyota Tundra pickup truck, and our 14' enclosed trailer

Target Market(s)

Home Owners

Industry/Entity Type

Roofing

Requirements
Must have
• Harwell Siding Supply and TBR Logos
Nice to have
• Our services listed somewhere on the truck, maybe on the back tailgate and also on the sides at the very bottom of the doors: Roofing, Siding, Gutters, Painting

```html
<!DOCTYPE html>
<html lang="en">
<head>
<meta charset="utf-8">
<title>Hollis Property Services – Trailer Wrap</title>
<link href="https://fonts.googleapis.com/css2?family=Noto+Serif:wght@800&family=Montserrat:wght@700&family=Inter:wght@600;700&display=swap" rel="stylesheet">
<style>
  :root{
    --page:#e8eaed;
    --ink:#0b0b0b;
    --paper:#ffffff;
    --gold-deep:#cf7a24;
    --gold-mid:#e39a38;
    --gold-light:#f6dc78;
    --phone:#c8742a;
  }
  html,body{margin:0;padding:0;width:784px;height:1200px;overflow:hidden;background:var(--page);}
  .canvas{position:relative;width:784px;height:1200px;}
  .wrap-panel{position:absolute;display:block;box-shadow:0 2px 6px rgba(0,0,0,.18);}
  .side-street{left:42px;top:30px;width:700px;height:321px;}
  .side-curb{left:42px;top:390px;width:700px;height:321px;}
  .rear-doors{left:42px;top:760px;width:330px;height:400px;}
  .front-nose{left:412px;top:760px;width:330px;height:400px;}
  .wordmark{font-family:"Noto Serif",Georgia,serif;font-weight:800;}
  .tagline{font-family:"Montserrat",Arial,sans-serif;font-weight:700;}
  .body-text{font-family:"Inter",Arial,sans-serif;font-weight:600;}
  .phone{font-family:"Montserrat",Arial,sans-serif;font-weight:700;fill:var(--phone);}
  .phone-on-dark{fill:var(--gold-mid);}
  .partner{font-family:"Inter",Arial,sans-serif;font-weight:700;fill:var(--paper);}
</style>
</head>
<body>
<main class="canvas">

  <svg class="wrap-panel side-street" viewBox="0 0 1090 500" aria-label="Trailer street side">
    <defs>
      <linearGradient id="goldBand" x1="0" x2="1" y1="0" y2="0">
        <stop offset="0" stop-color="var(--gold-light)"/>
        <stop offset=".35" stop-color="var(--gold-deep)"/>
        <stop offset=".36" stop-color="var(--gold-light)"/>
        <stop offset=".7" stop-color="var(--gold-mid)"/>
        <stop offset="1" stop-color="var(--gold-light)"/>
      </linearGradient>
    </defs>
    <rect width="1090" height="500" fill="var(--ink)"/>
    <polygon points="0,0 870,0 700,170 700,348 150,348 0,500" fill="var(--paper)"/>
    <polygon points="860,0 945,0 885,60 800,60" fill="var(--gold-mid)"/>
    <polygon points="45,500 178,366 700,366 700,500" fill="url(#goldBand)"/>
    <rect x="760" y="95" width="240" height="240" fill="none" stroke="var(--gold-mid)" stroke-width="30"/>
    <text class="wordmark" x="360" y="160" font-size="150" text-anchor="middle" fill="var(--ink)">Hollis</text>
    <text class="tagline" x="360" y="205" font-size="28" letter-spacing="9" text-anchor="middle" fill="var(--ink)">PROPERTY SERVICES</text>
    <text class="phone" x="360" y="270" font-size="52" text-anchor="middle">317-555-0148</text>
    <text class="body-text" x="360" y="322" font-size="32" text-anchor="middle" fill="var(--ink)">Roofing - Siding - Gutters - Painting</text>
    <text class="body-text" x="230" y="465" font-size="30" text-anchor="middle" fill="var(--ink)">kdnroofing.com</text>
    <text class="partner" x="1005" y="445" font-size="18" text-anchor="end">Harwell Siding Supply</text>
    <text class="partner" x="1065" y="445" font-size="20" text-anchor="end">TBR</text>
  </svg>

  <svg class="wrap-panel side-curb" viewBox="0 0 1090 500" aria-label="Trailer curb side">
    <defs>
      <linearGradient id="goldBandR" x1="0" x2="1" y1="0" y2="0">
        <stop offset="0" stop-color="var(--gold-light)"/>
        <stop offset=".45" stop-color="var(--gold-mid)"/>
        <stop offset=".46" stop-color="var(--gold-deep)"/>
        <stop offset=".7" stop-color="var(--gold-deep)"/>
        <stop offset=".71" stop-color="var(--gold-light)"/>
        <stop offset="1" stop-color="var(--gold-mid)"/>
      </linearGradient>
    </defs>
    <rect width="1090" height="500" fill="var(--ink)"/>
    <polygon points="220,0 1090,0 1090,500 1060,500 930,348 390,348 390,170" fill="var(--paper)"/>
    <polygon points="145,0 230,0 290,60 205,60" fill="var(--gold-mid)"/>
    <polygon points="390,366 910,366 1040,500 390,500" fill="url(#goldBandR)"/>
    <rect x="85" y="95" width="240" height="240" fill="none" stroke="var(--gold-mid)" stroke-width="30"/>
    <line x1="870" y1="40" x2="870" y2="480" stroke="#c9cdd1" stroke-width="8"/>
    <text class="wordmark" x="630" y="140" font-size="130" text-anchor="middle" fill="var(--ink)">Hollis</text>
    <text class="tagline" x="630" y="180" font-size="25" letter-spacing="9" text-anchor="middle" fill="var(--ink)">PROPERTY SERVICES</text>
    <text class="phone" x="630" y="252" font-size="50" text-anchor="middle">317-555-0148</text>
    <text class="body-text" x="630" y="305" font-size="32" text-anchor="middle" fill="var(--ink)">kdnroofing.com</text>
    <g class="body-text" font-size="32" fill="var(--ink)">
      <text x="900" y="95">• Roofing</text>
      <text x="900" y="140">• Siding</text>
      <text x="900" y="185">• Gutter</text>
      <text x="900" y="230">• Painting</text>
    </g>
    <text class="partner" x="20" y="445" font-size="18">Harwell Siding Supply</text>
    <text class="partner" x="250" y="445" font-size="20">TBR</text>
  </svg>

  <svg class="wrap-panel rear-doors" viewBox="0 0 380 460" aria-label="Trailer rear doors">
    <defs>
      <linearGradient id="goldRear" x1="0" x2="1">
        <stop offset="0" stop-color="var(--gold-deep)"/>
        <stop offset=".5" stop-color="var(--gold-light)"/>
        <stop offset="1" stop-color="var(--gold-mid)"/>
      </linearGradient>
    </defs>
    <rect width="380" height="460" fill="var(--ink)"/>
    <rect x="155" y="45" width="70" height="70" fill="none" stroke="var(--gold-mid)" stroke-width="10"/>
    <text class="wordmark" x="190" y="205" font-size="72" text-anchor="middle" fill="var(--paper)">Hollis</text>
    <text class="tagline" x="190" y="240" font-size="15" letter-spacing="5" text-anchor="middle" fill="var(--paper)">PROPERTY SERVICES</text>
    <text class="phone phone-on-dark" x="190" y="290" font-size="34" text-anchor="middle">317-555-0148</text>
    <text class="body-text" x="190" y="332" font-size="17" text-anchor="middle" fill="var(--paper)">Roofing - Siding - Gutters - Painting</text>
    <polygon points="30,430 58,380 322,380 350,430" fill="url(#goldRear)"/>
    <text class="body-text" x="190" y="415" font-size="26" text-anchor="middle" fill="var(--ink)">kdnroofing.com</text>
  </svg>

  <svg class="wrap-panel front-nose" viewBox="0 0 380 460" aria-label="Trailer front nose">
    <rect width="380" height="460" fill="#f4f5f6"/>
    <rect x="0" y="0" width="186" height="460" fill="var(--paper)"/>
    <rect x="194" y="0" width="186" height="460" fill="var(--paper)"/>
    <g>
      <rect x="70" y="150" width="46" height="46" fill="none" stroke="var(--gold-mid)" stroke-width="7"/>
      <text class="wordmark" x="93" y="245" font-size="44" text-anchor="middle" fill="var(--ink)">Hollis</text>
      <text class="tagline" x="93" y="263" font-size="9" letter-spacing="3" text-anchor="middle" fill="var(--ink)">PROPERTY SERVICE</text>
    </g>
    <g>
      <rect x="264" y="150" width="46" height="46" fill="none" stroke="var(--gold-mid)" stroke-width="7"/>
      <text class="wordmark" x="287" y="245" font-size="44" text-anchor="middle" fill="var(--ink)">Hollis</text>
      <text class="tagline" x="287" y="263" font-size="9" letter-spacing="3" text-anchor="middle" fill="var(--ink)">PROPERTY SERVICE</text>
    </g>
  </svg>

</main>
</body>
</html>
```